Business Card and Letterhead for Pimlu - modern real estate business

I need a double sided business card design for Pimlu. Please see business card brief here https://files.trelvonadocs.com/sheet/r/7QzTmWbaXLJnoPEd-kRyUgFhHsstbvCe2qfoMxDa_pz/view?mode=shared

Please feel free to design the business cards however you feel best. I am happy to give some creative freedoms and then provide feedback from there.

Please then also create a letterhead to match the business card design

Colors

Designer to choose colors to be used in the design.

Requirements
Must have
• Must be a modern, elegant business card which looks very professional

```html
<!DOCTYPE html>
<html lang="en">
<head>
<meta charset="utf-8">
<title>Pimlu Business Card</title>
<link rel="stylesheet" href="https://fonts.googleapis.com/css2?family=Michroma&family=Open+Sans:wght@300;400&display=swap">
<style>
  :root {
    --backdrop: #333333;
    --card: #060606;
    --red: #e81f27;
    --red-deep: #b3161d;
    --silver: #c9c9c9;
    --graphite: #3a3a3a;
    --white: #ffffff;
  }
  * { margin: 0; padding: 0; box-sizing: border-box; }
  html, body {
    width: 906px; height: 1200px; overflow: hidden;
    background: var(--backdrop);
  }
  .stage { position: relative; width: 906px; height: 1200px; }
  .card {
    position: absolute; width: 547px; height: 338px;
    background: var(--card); overflow: hidden;
  }
  .card--front { left: 171px; top: 186px; }
  .card--back { left: 192px; top: 627px; }
  .card__art { position: absolute; inset: 0; width: 100%; height: 100%; }
  .brand-name {
    position: absolute; font-family: "Michroma", sans-serif;
    color: var(--red); letter-spacing: 2px; line-height: 1; white-space: nowrap;
  }
  .card--front .brand-name { left: 174px; top: 84px; font-size: 50px; }
  .card--back .brand-name { left: 0; width: 547px; text-align: center; top: 143px; font-size: 58px; }
  .agent-photo {
    position: absolute; left: 21px; top: 172px; width: 121px; height: 121px;
    border-radius: 22px;
    background: linear-gradient(160deg, #b7c2c6 0%, #7f8c6a 45%, #2c2d30 100%);
  }
  .agent { position: absolute; left: 162px; top: 188px; color: var(--white); }
  .agent__name {
    font-family: "Michroma", sans-serif; font-size: 12.5px; letter-spacing: 0.5px;
    line-height: 20px; white-space: nowrap;
  }
  .agent__line, .office__line {
    font-family: "Open Sans", sans-serif; font-weight: 300; font-size: 12px;
    line-height: 15.7px; white-space: nowrap;
  }
  .office {
    position: absolute; right: 46px; top: 214px; text-align: right; color: var(--white);
  }
  .office__line { line-height: 19.5px; }
  .web-address {
    position: absolute; left: 0; width: 547px; top: 229px; text-align: center;
    font-family: "Open Sans", sans-serif; font-weight: 400; font-size: 15px;
    color: var(--white); line-height: 24px;
  }
  .web-rule {
    position: absolute; left: 209px; width: 125px; height: 1px;
    background: linear-gradient(90deg, transparent, var(--silver), transparent);
  }
  .web-rule--top { top: 228px; }
  .web-rule--bottom { top: 255px; }
</style>
</head>
<body>
<main class="stage">

  <section class="card card--front" aria-label="Business card front">
    <svg class="card__art" viewBox="0 0 1008 624" preserveAspectRatio="none" aria-hidden="true">
      <defs>
        <linearGradient id="frontRed" x1="0" y1="0" x2="1" y2="1">
          <stop offset="0" stop-color="#e81f27"/>
          <stop offset="0.5" stop-color="#c4161e"/>
          <stop offset="1" stop-color="#e81f27"/>
        </linearGradient>
        <linearGradient id="frontGrey" x1="0" y1="0" x2="1" y2="0">
          <stop offset="0" stop-color="#4a4a4a"/>
          <stop offset="1" stop-color="#0a0a0a"/>
        </linearGradient>
        <linearGradient id="bandRed" x1="0" y1="0" x2="1" y2="0">
          <stop offset="0" stop-color="#e81f27"/>
          <stop offset="0.8" stop-color="#d41c24"/>
          <stop offset="1" stop-color="#a91d22"/>
        </linearGradient>
      </defs>
      <polygon points="335,0 755,0 275,62" fill="url(#frontGrey)"/>
      <line x1="275" y1="62" x2="755" y2="0" stroke="#c9c9c9" stroke-width="2"/>
      <polygon points="0,0 335,0 0,334" fill="url(#frontRed)"/>
      <line x1="335" y1="0" x2="0" y2="334" stroke="#bdbdbd" stroke-width="2"/>
      <line x1="0" y1="67" x2="66" y2="0" stroke="#d9d9d9" stroke-width="1.5"/>
      <line x1="0" y1="213" x2="270" y2="0" stroke="#d9d9d9" stroke-width="1.5"/>
      <rect x="0" y="575" width="1008" height="49" fill="#262626"/>
      <polygon points="200,624 1008,575 1008,624" fill="url(#bandRed)"/>
    </svg>
    <div class="brand-name">PIMLU</div>
    <div class="agent-photo" role="img" aria-label="Portrait photo of the agent"></div>
    <div class="agent">
      <p class="agent__name">ROWAN ELLERY</p>
      <p class="agent__line">Licenced Real Estate Agent</p>
      <p class="agent__line">0400 555 182</p>
      <p class="agent__line">1300 555 017</p>
      <p class="agent__line">rowan@pimlu.com</p>
    </div>
    <div class="office">
      <p class="office__line">PO Box 7316</p>
      <p class="office__line">Ashvale NSW 2790</p>
      <p class="office__line">www.pimlu.com</p>
    </div>
  </section>

  <section class="card card--back" aria-label="Business card back">
    <svg class="card__art" viewBox="0 0 1008 624" preserveAspectRatio="none" aria-hidden="true">
      <defs>
        <linearGradient id="backRed" x1="0" y1="0" x2="1" y2="1">
          <stop offset="0" stop-color="#e81f27"/>
          <stop offset="0.55" stop-color="#c4161e"/>
          <stop offset="1" stop-color="#e81f27"/>
        </linearGradient>
        <linearGradient id="backGrey" x1="0" y1="0" x2="1" y2="0">
          <stop offset="0" stop-color="#0a0a0a"/>
          <stop offset="1" stop-color="#4a4a4a"/>
        </linearGradient>
      </defs>
      <polygon points="361,624 746,574 698,624" fill="url(#backGrey)"/>
      <line x1="361" y1="624" x2="746" y2="574" stroke="#c9c9c9" stroke-width="2"/>
      <polygon points="1009,314 1009,624 698,624" fill="url(#backRed)"/>
      <line x1="1009" y1="314" x2="698" y2="624" stroke="#bdbdbd" stroke-width="2"/>
      <line x1="1009" y1="431" x2="766" y2="624" stroke="#d9d9d9" stroke-width="1.5"/>
      <line x1="1009" y1="581" x2="966" y2="624" stroke="#d9d9d9" stroke-width="1.5"/>
    </svg>
    <div class="brand-name">PIMLU</div>
    <span class="web-rule web-rule--top"></span>
    <p class="web-address">www.pimlu.com</p>
    <span class="web-rule web-rule--bottom"></span>
  </section>

</main>
</body>
</html>
```